Marlo Tidecrest SUP Boards

We are a 100% owned and operated Australian Stand Up Paddle Board company, specialising in online sales of Stand Up Paddle Board packages.

We want our website to have an ocean, sunset, beach warm feel.

We sell 4 packages and need to be able to edit content and upload a number of photos of each package for sale.

Customers will be able to email us to receive quotes on freight costs and then pay via CoinLark only. We will have a Chatterbox page and Swapnest adds that need to be linked to the website also.

Target Market(s)

Surfers and Stand up paddle boarders

Industry/Entity Type

It Company

Number of Pages Required

3 page

Requirements
Must have
• Link to CoinLark for payment
• Link to Chatterbox page
• Three tabs- Welcome page, SUP Boards and a Contact us page

```html
<!DOCTYPE html>
<html lang="en">
<head>
<meta charset="utf-8">
<title>Marlo Tidecrest SUP Boards</title>
<link href="https://fonts.googleapis.com/css2?family=Nunito+Sans:wght@400;600;700;800&display=swap" rel="stylesheet">
<style>
  :root {
    --orange: #e8861f;
    --orange-deep: #d9721a;
    --sun: #ffd21a;
    --ink: #1f1a14;
    --white: #ffffff;
    --field: #f3f3f3;
    --field-line: #d6d6d6;
    --muted: #333333;
    --paybtn: #1e5d95;
  }
  * { box-sizing: border-box; margin: 0; padding: 0; }
  html, body { width: 1127px; height: 1200px; overflow: hidden; }
  body {
    position: relative;
    font-family: "Nunito Sans", sans-serif;
    color: var(--ink);
  }
  .backdrop {
    position: absolute; inset: 0;
    background:
      radial-gradient(ellipse at 30% 40%, rgba(255,205,90,.9), transparent 55%),
      radial-gradient(ellipse at 85% 35%, rgba(240,200,150,.8), transparent 50%),
      linear-gradient(180deg, #6b3a12 0%, #c97a2a 30%, #e3a048 60%, #9a5a1e 85%, #5a2e0c 100%);
  }
  .site-header {
    position: absolute; left: 0; top: 0; width: 1127px; height: 102px;
    background: var(--orange);
  }
  .brand {
    position: absolute; left: 173px; top: 0; width: 270px; height: 102px;
    background: radial-gradient(ellipse at 50% 50%, var(--sun) 0%, #f4b414 55%, var(--orange) 100%);
    display: flex; align-items: center; justify-content: center;
  }
  .brand-name {
    font-weight: 800; font-size: 19px; color: var(--ink); line-height: 1.1; text-align: center;
  }
  .main-nav { position: absolute; top: 0; left: 0; }
  .main-nav a {
    position: absolute; top: 44px; font-weight: 700; font-size: 16px;
    color: var(--white); text-decoration: none; letter-spacing: .3px; white-space: nowrap;
  }
  .nav-active-bar {
    position: absolute; left: 708px; top: 102px; width: 101px; height: 4px; background: var(--sun);
  }
  .pay-button {
    position: absolute; left: 828px; top: 130px; width: 124px; height: 29px;
    background: linear-gradient(#3b7cc0, var(--paybtn));
    border: 1px solid #9fc0e0; border-radius: 3px;
    color: var(--white); font-size: 11px; font-weight: 700;
    display: flex; align-items: center; justify-content: center; gap: 4px;
  }
  .pay-button span { font-weight: 400; }
  .panel {
    position: absolute; left: 173px; top: 174px; width: 781px; height: 943px; background: var(--white);
  }
  .hero {
    position: absolute; left: 0; top: 0; width: 781px; height: 426px;
    background: linear-gradient(180deg, #c8361a 0%, #e4561e 35%, #f0781f 55%, #a8300f 75%, #1a0804 100%);
    display: flex; align-items: center; justify-content: center;
  }
  .hero-name {
    position: absolute; top: 150px; width: 100%; text-align: center;
    font-weight: 800; font-size: 26px; color: var(--sun);
  }
  .hero-dots { position: absolute; top: 374px; left: 0; }
  .hero-dots i {
    position: absolute; width: 10px; height: 10px; border-radius: 50%; background: var(--white);
  }
  .hero-dots i.on { background: #f3b400; }
  .section-title {
    position: absolute; top: 440px; width: 100%; text-align: center;
    color: var(--orange); font-weight: 800; font-size: 24px; letter-spacing: .3px;
  }
  .field {
    position: absolute; top: 490px; height: 43px;
    background: var(--field); border: 1px solid var(--field-line); border-radius: 3px;
    font-size: 15px; color: var(--muted); padding-left: 10px;
    display: flex; align-items: center;
  }
  .field svg { position: absolute; right: 9px; top: 14px; }
  .upload-btn {
    position: absolute; left: 609px; top: 491px; width: 159px; height: 42px;
    background: var(--orange); border-radius: 3px; color: var(--white);
    font-size: 15px; font-weight: 600; display: flex; align-items: center; justify-content: center;
  }
  .gallery-band {
    position: absolute; left: 12px; top: 552px; width: 745px; height: 38px;
    background: linear-gradient(90deg, rgba(230,230,230,.6), rgba(245,245,245,.3) 70%, transparent);
  }
  .gallery-label {
    position: absolute; left: 12px; top: 570px; font-size: 12px; font-weight: 600; color: var(--ink);
  }
  .gallery-arrows { position: absolute; left: 745px; top: 571px; }
  .card {
    position: absolute; width: 236px; height: 133px; overflow: hidden;
  }
  .card .shot { position: absolute; inset: 0; }
  .card .caption {
    position: absolute; left: 0; bottom: 0; width: 100%; height: 25px;
    background: rgba(20,20,20,.55); color: var(--white);
    display: flex; align-items: center; justify-content: space-between; padding: 0 8px 0 15px;
  }
  .caption b { font-size: 10px; font-weight: 800; }
  .caption span { font-size: 9px; }
  .site-footer {
    position: absolute; left: 0; top: 1134px; width: 1127px; text-align: center; color: var(--white);
  }
  .footer-links { font-size: 14px; }
  .footer-links a { color: var(--white); text-decoration: none; padding: 0 11px; }
  .footer-links em { font-style: normal; }
  .copyright { font-size: 14px; margin-top: 6px; }
</style>
</head>
<body>
  <div class="backdrop" role="img" aria-label="Blurred tropical beach sunset with palm fronds"></div>

  <header class="site-header">
    <div class="brand"><span class="brand-name">Marlo Tidecrest<br>SUP Boards</span></div>
    <nav class="main-nav">
      <a href="#" style="left:597px">WELCOME</a>
      <a href="#" style="left:711px">SUP BOARDS</a>
      <a href="#" style="left:844px">CONTACT US</a>
    </nav>
  </header>
  <div class="nav-active-bar"></div>

  <a class="pay-button" href="#"><span>Pay using</span> CoinLark</a>

  <main class="panel">
    <div class="hero" role="img" aria-label="Fiery orange sunset sky over silhouetted palm trees">
      <div class="hero-name">Marlo Tidecrest SUP Boards</div>
      <div class="hero-dots">
        <i class="on" style="left:352px"></i>
        <i style="left:374px"></i>
        <i style="left:394px"></i>
        <i style="left:417px"></i>
      </div>
    </div>

    <h1 class="section-title">SUP BOARDS</h1>

    <div class="field" style="left:12px;width:391px">Photos
      <svg width="16" height="13" viewBox="0 0 16 13"><path d="M0 1h5l1.5 1.5H13v2H3L0 11z M3 5h13l-3 8H0z" fill="#555"/></svg>
    </div>
    <div class="field" style="left:417px;width:177px">Package
      <svg width="10" height="8" viewBox="0 0 10 8" style="top:17px"><path d="M0 0h10L5 8z" fill="#111"/></svg>
    </div>
    <div class="upload-btn">UPLOAD</div>

    <div class="gallery-band"></div>
    <div class="gallery-label">UPLOADED PHOTOS</div>
    <svg class="gallery-arrows" width="22" height="12" viewBox="0 0 22 12"><path d="M6 1L1 6l5 5M16 1l5 5-5 5" stroke="#222" stroke-width="1.6" fill="none"/></svg>

    <div class="card" style="left:12px;top:595px">
      <div class="shot" role="img" aria-label="Paddle boarder on a lake under a blue sky" style="background:linear-gradient(180deg,#5f86b4,#b8a98f 60%,#7a8a96)"></div>
      <div class="caption"><b>SUP BOARDS</b><span>Posted : 2hrs 4mints</span></div>
    </div>
    <div class="card" style="left:272px;top:595px">
      <div class="shot" role="img" aria-label="Paddle boarder standing against a bright blue sky" style="background:linear-gradient(180deg,#1f7fd0,#5aa8e8 60%,#2b6fa8)"></div>
      <div class="caption"><b>SUP BOARDS</b><span>Posted : 2hrs 4mints</span></div>
    </div>
    <div class="card" style="left:533px;top:595px">
      <div class="shot" role="img" aria-label="Paddle boarder on a yellow board near a tropical island" style="background:linear-gradient(180deg,#2d7ad0,#8fc0e6 45%,#3f8a3a 70%,#e8c32a)"></div>
      <div class="caption"><b>SUP BOARDS</b><span>Posted : 2hrs 4mints</span></div>
    </div>
    <div class="card" style="left:12px;top:756px">
      <div class="shot" role="img" aria-label="Paddle boarder splashing through river water" style="background:linear-gradient(180deg,#8a8f74,#a9b0a8 45%,#5d7390)"></div>
      <div class="caption"><b>SUP BOARDS</b><span>Posted : 2hrs 4mints</span></div>
    </div>
    <div class="card" style="left:272px;top:756px">
      <div class="shot" role="img" aria-label="Child paddle boarding by a palm-lined beach" style="background:linear-gradient(180deg,#2f6fc0,#3e7f3a 40%,#e6dcc4 62%,#38b6b0)"></div>
      <div class="caption"><b>SUP BOARDS</b><span>Posted : 2hrs 4mints</span></div>
    </div>
    <div class="card" style="left:533px;top:756px">
      <div class="shot" role="img" aria-label="Paddle boarder on calm water with a pastel colour cast" style="background:linear-gradient(120deg,#e06ad0,#f0e8a0 40%,#a8e0b0 65%,#8aa8f0)"></div>
      <div class="caption"><b>SUP BOARDS</b><span>Posted : 2hrs 4mints</span></div>
    </div>
  </main>

  <footer class="site-footer">
    <div class="footer-links">
      <a href="#">Home</a><em>|</em><a href="#">About Us</a><em>|</em><a href="#">Services</a><em>|</em><a href="#">Packages</a><em>|</em><a href="#">Contact Us</a>
    </div>
    <div class="copyright">© 2014&nbsp; Company Name , All Right&nbsp; Reserved</div>
  </footer>
</body>
</html>
```